Bramble Sort This

Just like the other work you have done for us, we need a new flyer for another package. Will upload all the info.
Not sure if you wanted to use one/all of the ties.
Please change the image with "Bramble Crew" on the back of the computer and maybe his tie colour to green?
Trying to get it to print asap so would be great if you had time to get it done.
Thank you in advance!

Work

• The usual web address, email and phone number

```html
<!DOCTYPE html>
<html lang="en">
<head>
<meta charset="utf-8">
<title>Bramble Sort This – Bramble Crew</title>
<link rel="stylesheet" href="https://fonts.googleapis.com/css2?family=Anton&family=Arimo:wght@400;700&family=PT+Sans&display=swap">
<style>
  :root {
    --cyan: #1ebfdf;
    --ink: #111111;
    --panel: #1d1d1d;
    --white: #ffffff;
    --muted: #e6e6e6;
  }
  html, body { margin: 0; padding: 0; }
  body {
    width: 927px; height: 1200px; overflow: hidden;
    background: var(--white);
    font-family: "Arimo", Arial, sans-serif;
  }
  .flyer { position: relative; width: 927px; height: 1200px; overflow: hidden; }

  .top-rule { position: absolute; left: 0; top: 0; width: 927px; height: 6px; background: var(--cyan); }

  .hero { position: absolute; left: 0; top: 6px; width: 927px; height: 506px;
    background: linear-gradient(90deg, #ececec 0%, #ffffff 45%, #ffffff 100%); }
  .hero-photo { position: absolute; left: 25px; top: 40px; width: 320px; height: 466px;
    background: linear-gradient(180deg, #d8d8d8 0%, #b9b9b9 55%, #2a2a2a 100%);
    border-radius: 140px 140px 0 0; }

  .headline { position: absolute; right: 58px; top: 34px; margin: 0; text-align: right;
    font-family: "Anton", Impact, sans-serif; font-weight: 400; font-size: 66px; line-height: 69px;
    color: var(--ink); letter-spacing: -0.5px; }
  .headline .accent { color: var(--cyan); }

  .subline { position: absolute; right: 62px; top: 390px; margin: 0; text-align: right;
    font-family: "Anton", Impact, sans-serif; font-size: 30px; line-height: 47px; color: var(--ink);
    letter-spacing: 0.5px; }

  .divider { position: absolute; left: 0; top: 512px; width: 927px; height: 6px; background: var(--cyan); }

  .offer { position: absolute; left: 0; top: 518px; width: 927px; height: 677px; background: var(--panel); color: var(--white); }
  .bottom-rule { position: absolute; left: 0; top: 1195px; width: 927px; height: 5px; background: var(--cyan); }

  .brand-line { position: absolute; left: 0; top: 38px; width: 927px; margin: 0; text-align: center;
    font-family: "Anton", Impact, sans-serif; font-weight: 400; font-size: 46px; line-height: 60px; }
  .brand-mark { display: inline-block; width: 14px; height: 14px; background: var(--white); margin-right: 12px; vertical-align: middle; }
  .brand-name { margin-right: 20px; }

  .package-title { position: absolute; left: 38px; top: 122px; margin: 0;
    font-family: "Anton", Impact, sans-serif; font-weight: 400; font-size: 31px; line-height: 40px; color: var(--cyan); }

  .inclusions { position: absolute; left: 38px; top: 192px; width: 560px; margin: 0; padding: 0; list-style: none;
    font-size: 19px; line-height: 25px; }
  .inclusions li { padding-left: 14px; text-indent: -14px; }
  .inclusions li::before { content: "•"; color: var(--cyan); display: inline-block; width: 14px; text-indent: 0; }

  .problems { position: absolute; left: 38px; top: 395px; width: 520px; margin: 0; padding: 0; list-style: none;
    font-size: 15px; line-height: 27px; }
  .problems li { position: relative; padding-left: 18px; }
  .problems li::before { content: ""; position: absolute; left: 2px; top: 11px; width: 5px; height: 5px; background: var(--cyan); }

  .price-badge { position: absolute; left: 618px; top: 148px; width: 244px; height: 244px; }
  .price { position: absolute; left: 618px; top: 148px; width: 244px; height: 244px; margin: 0;
    display: flex; align-items: center; justify-content: center;
    font-family: "PT Sans", "Myriad Pro", sans-serif; font-size: 80px; color: var(--white); letter-spacing: -1px; }
  .price-note { position: absolute; left: 630px; top: 423px; margin: 0; font-size: 17px; }
  .price-note span { color: var(--cyan); }

  .booking { position: absolute; left: 610px; top: 500px; margin: 0; text-align: center; width: 270px; }
  .booking-call { margin: 0; font-weight: 700; font-size: 54px; line-height: 60px; }
  .booking-web { margin: 2px 0 0; font-weight: 700; font-size: 22px; line-height: 26px; color: var(--cyan); }
  .booking-phone, .booking-email { margin: 0; font-size: 18px; line-height: 25px; }
</style>
</head>
<body>
<main class="flyer">
  <div class="top-rule"></div>

  <section class="hero">
    <div class="hero-photo" role="img" aria-label="Smiling technician in a grey suit and green tie holding a laptop marked Bramble Crew and giving an OK sign"></div>
    <h1 class="headline"><span class="accent">Need Help</span><br>to sort out<br>your technology<br>at <span class="accent">home?</span></h1>
    <p class="subline">Whatever the issue big or small<br>and even if you aren’t surewhat it is,</p>
  </section>

  <div class="divider"></div>

  <section class="offer">
    <h2 class="brand-line"><span class="brand-mark"></span><span class="brand-name">Bramble Crew</span>Can help</h2>

    <h3 class="package-title">BRAMBLE SORT THIS</h3>
    <ul class="inclusions">
      <li>An in-person visit by a Geek to your home for 2 hours*</li>
      <li>Pre-online assessment so your Geek is fully prepared and ready to go for the visit</li>
      <li>IT Health Report card</li>
      <li>Bramble Crew Membership entitling you to priority bookings, discounts and special offers</li>
      <li>Cool Bramble Crew fridge magnet</li>
    </ul>

    <svg class="price-badge" viewBox="-122 -122 244 244" aria-hidden="true">
      <g fill="var(--cyan)">
        <rect x="-83.5" y="-83.5" width="167" height="167" transform="rotate(0)"/>
        <rect x="-83.5" y="-83.5" width="167" height="167" transform="rotate(11.25)"/>
        <rect x="-83.5" y="-83.5" width="167" height="167" transform="rotate(22.5)"/>
        <rect x="-83.5" y="-83.5" width="167" height="167" transform="rotate(33.75)"/>
        <rect x="-83.5" y="-83.5" width="167" height="167" transform="rotate(45)"/>
        <rect x="-83.5" y="-83.5" width="167" height="167" transform="rotate(56.25)"/>
        <rect x="-83.5" y="-83.5" width="167" height="167" transform="rotate(67.5)"/>
        <rect x="-83.5" y="-83.5" width="167" height="167" transform="rotate(78.75)"/>
      </g>
    </svg>
    <p class="price">$195</p>
    <p class="price-note"><span>*</span>Price is inclusive of travel</p>

    <ul class="problems">
      <li>A Lumo TV, Playvault or printer that you can’t get working?</li>
      <li>Wireless that is running at the speed of a snail?</li>
      <li>Need to back up all your photos? No idea how to sync Tunebox across all your devices?</li>
      <li>Need help in backing up all your files ?</li>
      <li>Updated software that needs to be installed on your computer?</li>
      <li>Too many devices and not sure how to utilise them all in the best way?</li>
    </ul>

    <div class="booking">
      <p class="booking-call">Book Now</p>
      <p class="booking-web">www.bramblecrew.asia</p>
      <p class="booking-phone">Singapore Hotline - 6100 2468</p>
      <p class="booking-email">Email - booking@bramblecrew.asia</p>
    </div>
  </section>

  <div class="bottom-rule"></div>
</main>
</body>
</html>
```